Coffee House With Cycling Theme Wants Business Cards

We want to create a business card for a coffee house that has a cycling theme. We expect to use the current logo on one side of the business card and we have been considering adding the words 'COFFEE HOUSE' underneath (see example). For the other side of the business card we want an interesting design with tag-line, address and social media links (the normal business card stuff). See examples provided but we are not fixed on having it exactly as shown, we are very open to great creative ideas. Please note our logo has the initials ‘KR' in orange embedded in the design and this must be retained. However, you can play with the words COFFEE HOUSE as well as use the orange color on the backside of the business card, as you see fit. For an image on the backside of the business card it can be a photo, hand-drawn or whatever but it must visually combine coffee and cycling in some way. The interior of the Coffee House will be reclaimed wood, rustic and have an urban feel to it with cycling artifacts hanging from the walls/ceiling, etc. Finally, it would be beneficial if the business card design elements can be easily used on flyers and other promotional assets. Good luck, we are looking forward to seeing your creative ideas.

Target Market(s)

Coffee lovers and cycling fans

Contact Information for Business Card

See project description.

Colors

Designer to choose colors to be used in the design.

Requirements
Must have
• Must use the current logo provided and combine a coffee and bike theme.
Nice to have
• Orange is used in current logo and could be used as an accent color on the backside of the business card.

```html
<!DOCTYPE html>
<html lang="en">
<head>
<meta charset="utf-8">
<title>KR Coffee House – Business Card</title>
<link rel="stylesheet" href="https://fonts.googleapis.com/css2?family=Lato:wght@400;700&family=Open+Sans:wght@400;600&display=swap">
<style>
  :root {
    --backdrop: #5e5e5e;
    --paper: #eeeeee;
    --charcoal: #3d3d3d;
    --orange: #ff6a1f;
    --ink: #333333;
    --white: #ffffff;
    --bean-dark: #3a2416;
    --bean-mid: #7a4a2a;
    --road-sky: #8a8f98;
  }
  * { box-sizing: border-box; margin: 0; padding: 0; }
  html, body {
    width: 1200px; height: 1200px; overflow: hidden;
    background: var(--backdrop);
  }
  .canvas { position: relative; width: 1200px; height: 1200px; }

  .card {
    position: absolute; top: 310px;
    width: 364px; height: 594px; overflow: hidden;
  }
  .card--front { left: 234px; background: var(--paper); }
  .card--back { left: 628px; width: 369px; }

  /* front */
  .brand {
    position: absolute; top: 0; left: 0; width: 100%; height: 363px;
    text-align: center;
  }
  .brand__mark {
    position: absolute; top: 92px; left: 0; width: 100%;
    font-family: "Lato", sans-serif; font-weight: 700;
    font-size: 120px; line-height: 1; color: var(--orange);
    letter-spacing: 4px;
  }
  .brand__name {
    position: absolute; top: 242px; left: 0; width: 100%;
    font-family: "Lato", sans-serif; font-weight: 400;
    font-size: 36px; color: var(--orange); letter-spacing: 0.5px;
  }
  .brand__web {
    position: absolute; top: 300px; left: 0; width: 100%;
    font-family: "Open Sans", sans-serif; font-size: 18px; color: var(--ink);
  }
  .tagline {
    position: absolute; top: 363px; left: 0; width: 100%; height: 113px;
    background: var(--charcoal); text-align: center;
  }
  .tagline__title {
    margin-top: 25px;
    font-family: "Lato", sans-serif; font-weight: 700;
    font-size: 32px; line-height: 1; color: var(--orange);
  }
  .tagline__sub {
    margin-top: 9px;
    font-family: "Lato", sans-serif; font-size: 19px; color: var(--white);
  }
  .address {
    position: absolute; top: 476px; left: 0; width: 100%; height: 118px;
    background: var(--orange); text-align: center;
    font-family: "Open Sans", sans-serif; font-weight: 600;
    font-size: 17px; line-height: 24px; color: var(--white);
    padding-top: 28px;
  }

  /* back */
  .hero {
    position: absolute; inset: 0;
    background: linear-gradient(180deg,
      var(--bean-dark) 0%, var(--bean-mid) 30%, #b7723e 40%,
      #e9e2da 48%, #d9cfc4 58%, #4a3020 62%, #6d6f72 70%,
      var(--road-sky) 80%, #7d7a76 100%);
  }
  .social {
    position: absolute; left: 40px; top: 503px;
  }
  .social__links {
    display: flex; gap: 6px; margin-left: 22px;
  }
  .social__link {
    display: block; width: 36px; height: 36px; border-radius: 50%;
    background: var(--white);
  }
  .social__handle {
    margin-top: 6px;
    font-family: "Open Sans", sans-serif; font-size: 18.5px; color: var(--white);
  }
</style>
</head>
<body>
<main class="canvas">
  <section class="card card--front">
    <div class="brand">
      <div class="brand__mark">KR</div>
      <div class="brand__name">COFFEE HOUSE</div>
      <div class="brand__web">www.krcoffeehouse.com</div>
    </div>
    <div class="tagline">
      <div class="tagline__title">BEANS &amp; BIKES</div>
      <div class="tagline__sub">GET YOUR DAILY QUOTA</div>
    </div>
    <div class="address">
      501, Address Goes Here<br>Country Name, 123456
    </div>
  </section>

  <section class="card card--back">
    <div class="hero" role="img" aria-label="Photo montage: roasted coffee beans above a steaming white cup of coffee that becomes the body of a cyclist riding along a tree-lined road"></div>
    <div class="social">
      <div class="social__links">
        <span class="social__link" aria-label="Social profile one"></span>
        <span class="social__link" aria-label="Social profile two"></span>
      </div>
      <div class="social__handle">krcoffeehouse</div>
    </div>
  </section>
</main>
</body>
</html>
```